Psychiatric Office Needs a Website- 1st Time Ever!

Been in practice since 2003 with no website, but finally ready to dive in. We are Maplecrest Behavioral Healthcare, a mental health outpatient practice based in Fayetteville, Georgia that sees diverse individuals and families from childhood to advanced age for a variety of conditions. We've grown by word of mouth and referral but would now like to have a digital footprint. Be the pioneer of our website and we will be sure to share. We would like to see designs that are modern, animated, fairly colorful, easy to read, and caters to all ages. Also, we would like the design to take the whole page (not be centered) and can be viewed well on phone/tablet. Please see our outline for more information. Our motto/slogan is: Maplecrest Behavioral Healthcare- A step forward in your wellness journey, so the design should try to reflect that.
Updates

Project Deadline Extended
Reason: site in progress

Target Market(s)

Children through elderly

Industry/Entity Type

Medical

Logo Text

Stepping forward in your wellness journey

Number of Pages Required

1 page

Colors

Designer to choose colors to be used in the design.

Requirements
Must have
• Animation or moving pictures.
• Color.
• Concise.
• User friendly
• Diversity in the stock photos

```html
<!DOCTYPE html>
<html lang="en">
<head>
<meta charset="utf-8">
<title>Maplecrest Behavioral Healthcare</title>
<link href="https://fonts.googleapis.com/css2?family=Oswald:wght@500&family=Open+Sans:wght@400;600;700&family=Roboto:wght@500;700&display=swap" rel="stylesheet">
<style>
:root{
  --blue:#1a5fc0;
  --blue-dark:#114a9c;
  --green:#55ad0f;
  --green-light:#6cbf22;
  --text:#444;
  --muted:#666;
  --grey-bg:#efefef;
  --footer:#1c1c1c;
  --white:#fff;
}
*{margin:0;padding:0;box-sizing:border-box}
html,body{width:1200px;height:2970px;overflow:hidden;background:var(--white)}
body{font-family:"Open Sans",Arial,sans-serif;color:var(--text);position:relative}
.abs{position:absolute}

/* header */
.site-header{position:absolute;top:0;left:0;width:1200px;height:108px}
.brand{left:100px;top:32px}
.brand-name{font-family:"Open Sans",sans-serif;font-weight:600;font-size:30px;color:var(--green)}
.info{display:flex;align-items:center;gap:12px;font-size:13px;font-weight:700;line-height:18px}
.info .lbl{color:#333}
.info .val{color:var(--green)}
.info-hours{left:543px;top:36px}
.info-phone{left:812px;top:36px}
.portal{left:965px;top:38px;width:135px;height:42px;background:var(--green);color:var(--white);font-size:13px;font-weight:700;display:flex;align-items:center;justify-content:center;border-radius:2px}

/* nav */
.main-nav{top:108px;left:0;width:1200px;height:60px;background:var(--blue);display:flex;padding:0 100px;justify-content:space-between}
.main-nav a{color:var(--white);text-decoration:none;font-family:"Roboto",sans-serif;font-weight:500;font-size:15px;display:flex;align-items:center;padding:0 28px}
.main-nav a.active{background:var(--blue-dark);padding:0 56px}

/* hero */
.hero{top:168px;left:0;width:1200px;height:570px;background:linear-gradient(100deg,#b9b2a6 0%,#d9dbe0 35%,#8fa6cc 60%,#e3e6ec 100%)}
.hero-curve{position:absolute;left:0;bottom:0}
.hero-title{left:100px;top:100px;font-family:"Oswald",sans-serif;font-weight:500;font-size:52px;line-height:60px;color:var(--white);text-shadow:0 2px 4px rgba(0,0,0,.3)}
.hero-tag{left:100px;top:250px;font-size:27px;color:var(--white);text-shadow:0 2px 4px rgba(0,0,0,.35)}
.hero-btn{left:100px;top:326px;width:180px;height:50px;background:var(--blue);color:var(--white);border:2px solid var(--white);font-size:16px;font-weight:600;display:flex;align-items:center;justify-content:center}
.hero-arrow{top:210px}

/* section titles */
.sec-title{width:1200px;text-align:center;font-family:"Roboto",sans-serif;font-weight:700;font-size:26px;color:var(--blue)}
.sec-rule{width:82px;height:2px;background:var(--blue);left:559px}

/* services */
.svc-intro{top:856px;left:200px;width:800px;text-align:center;font-size:14px;line-height:28px;color:#333}
.svc-row{top:1003px;left:100px;width:1000px;height:205px;display:flex;box-shadow:0 16px 14px -10px rgba(0,0,0,.25)}
.svc-card{width:250px;height:205px;color:var(--white);text-align:center;position:relative;padding-top:78px}
.svc-card.green{background:var(--green)}
.svc-card.blue{background:var(--blue)}
.svc-icon{position:absolute;top:-52px;left:74px;width:102px;height:102px;border-radius:50%;border:4px solid var(--white);display:flex;align-items:center;justify-content:center}
.svc-card.green .svc-icon{background:var(--blue)}
.svc-card.blue .svc-icon{background:var(--green)}
.svc-name{font-family:"Roboto",sans-serif;font-weight:500;font-size:20px;margin-bottom:10px}
.svc-text{font-size:12px;line-height:20px;padding:0 36px;opacity:.9}
.svc-go{position:absolute;left:116px;bottom:14px}

/* conditions */
.conditions{top:1305px;left:0;width:1200px;height:385px;display:flex}
.cond-text{width:600px;height:385px;background:var(--green-light);color:var(--white);padding:48px 100px 0}
.cond-title{font-family:"Roboto",sans-serif;font-weight:500;font-size:26px;margin-bottom:22px}
.cond-item{display:flex;align-items:center;gap:14px;font-size:15px;font-weight:600;margin-bottom:14px}
.cond-sub{font-size:13.5px;line-height:22px;margin:8px 0 22px;opacity:.95}
.cond-photo{width:600px;height:385px;background:var(--white);padding:4px}
.cond-photo div{width:100%;height:100%;background:linear-gradient(110deg,#c8c4bd 0%,#d9a0a8 40%,#b8a591 70%,#7c5a55 100%)}

/* faq */
.faq-list{top:1853px;left:100px;width:480px}
.faq-q{height:46px;border:2px solid var(--green);border-radius:23px;display:flex;align-items:center;justify-content:space-between;padding:0 18px;font-size:14.5px;font-weight:600;color:var(--green);margin-bottom:14px;position:relative}
.faq-q.open{background:var(--green);color:var(--white)}
.faq-a{top:1860px;left:622px;width:480px}
.faq-a h3{font-family:"Open Sans",sans-serif;font-weight:600;font-size:20px;color:#222;margin-bottom:18px}
.tick-line{display:flex;align-items:center;gap:10px;font-size:14.5px;color:var(--green);margin-bottom:12px}
.faq-a p{font-size:13px;line-height:22px;color:#333;margin-top:18px}

/* news */
.news{top:2165px;left:0;width:1200px;height:430px;background:var(--grey-bg)}
.news-item{position:absolute;top:178px;display:flex;gap:20px}
.news-img{width:212px;height:158px}
.news-body{width:240px}
.news-body h4{font-family:"Open Sans",sans-serif;font-weight:600;font-size:16px;color:#222;margin:2px 0 12px}
.meta{display:flex;gap:14px;font-size:11px;color:var(--green);margin-bottom:12px}
.meta span{display:flex;align-items:center;gap:5px}
.news-body p{font-size:12.5px;line-height:21px;color:#333;text-align:justify}

/* footer */
.site-footer{top:2560px;left:0;width:1200px;height:410px;background:var(--footer);color:var(--white)}
.foot-notch{position:absolute;top:0;left:0}
.foot-title{top:122px;width:1200px;text-align:center;font-family:"Open Sans",sans-serif;font-weight:600;font-size:26px}
.foot-rule{top:162px;left:563px;width:74px;height:2px;background:var(--white)}
.foot-contact{top:218px;left:0;width:1200px;display:flex;justify-content:center;gap:44px;font-size:19px}
.foot-contact span{display:flex;align-items:center;gap:12px}
.foot-links{top:284px;left:0;width:1200px;display:flex;justify-content:center;gap:24px;font-size:14px;font-weight:600}
.foot-line{top:340px;left:100px;width:1000px;height:1px;background:#555}
.copyright{top:366px;left:100px;font-size:13.5px}
.social{top:354px;left:876px;display:flex;gap:14px}
.social span{width:38px;height:38px;border:2px solid var(--white);border-radius:50%}
</style>
</head>
<body>

<header class="site-header">
  <div class="abs brand"><span class="brand-name">Maplecrest</span></div>
  <div class="abs info info-hours">
    <svg width="34" height="34" viewBox="0 0 34 34"><circle cx="17" cy="17" r="15" fill="none" stroke="#1a5fc0" stroke-width="2"/><circle cx="17" cy="17" r="6" fill="none" stroke="#1a5fc0" stroke-width="2"/><path d="M17 13v4h3" stroke="#1a5fc0" stroke-width="2" fill="none"/></svg>
    <div><div><span class="lbl">HOURS OR </span><span class="val">&nbsp;MON TO FRI</span></div><div><span class="lbl">APPT TIMES: </span><span class="val">10A.M TO 5P.M</span></div></div>
  </div>
  <div class="abs info info-phone">
    <svg width="34" height="34" viewBox="0 0 34 34"><circle cx="17" cy="17" r="15" fill="none" stroke="#55ad0f" stroke-width="2"/><path d="M12 10l3 0 1.5 4-2 1.5a9 9 0 0 0 4 4l1.5-2 4 1.5v3a2 2 0 0 1-2 2A13 13 0 0 1 10 12a2 2 0 0 1 2-2z" fill="#55ad0f"/></svg>
    <div><div class="val">PHONE:</div><div class="val">180 047 3918</div></div>
  </div>
  <div class="abs portal">PATIENT PORTAL</div>
</header>

<nav class="abs main-nav">
  <a class="active">HOME</a><a>ABOUT US</a><a>SERVICES</a><a>CONDITIONS WE TREAT</a><a>NEW PATIENTS</a><a>CONTACT US</a>
</nav>

<section class="abs hero" role="img" aria-label="Photo of a nurse reading a chart with a young boy in a clinic">
  <h1 class="abs hero-title">Maplecrest Behavioral<br>Healthcare</h1>
  <p class="abs hero-tag">A step forward in your wellness journey</p>
  <div class="abs hero-btn">TAKE A SCREENING</div>
  <svg class="abs hero-arrow" style="left:28px" width="30" height="56" viewBox="0 0 30 56"><path d="M26 2L4 28l22 26" fill="none" stroke="#fff" stroke-width="2"/></svg>
  <svg class="abs hero-arrow" style="left:1142px" width="30" height="56" viewBox="0 0 30 56"><path d="M4 2l22 26L4 54" fill="none" stroke="#fff" stroke-width="2"/></svg>
  <svg class="hero-curve" width="1200" height="70" viewBox="0 0 1200 70" preserveAspectRatio="none"><path d="M0 0Q600 95 1200 0V70H0z" fill="#fff"/></svg>
</section>

<h2 class="abs sec-title" style="top:800px">MAPLECREST SERVICES</h2>
<p class="abs svc-intro">To be the leading provider of outpatient psychiatric care in Atlanta Metro South, working together to promote (the) mental wellness of our community.</p>

<div class="abs svc-row">
  <div class="svc-card green">
    <div class="svc-icon"><svg width="46" height="46" viewBox="0 0 46 46"><path d="M23 12c-3-5-11-3-9 4 1 4 9 9 9 9s8-5 9-9c2-7-6-9-9-4z" fill="#fff"/><path d="M4 26l10 8h14M42 26l-10 8" fill="none" stroke="#fff" stroke-width="3"/></svg></div>
    <div class="svc-name">TELEPSYCHIATRY</div>
    <div class="svc-text">To be the leading provider of outpatient psychiatric care.</div>
    <svg class="svc-go" width="18" height="18" viewBox="0 0 18 18"><circle cx="9" cy="9" r="9" fill="#fff"/><path d="M5 9h7M9 5l4 4-4 4" fill="none" stroke="#55ad0f" stroke-width="2"/></svg>
  </div>
  <div class="svc-card blue">
    <div class="svc-icon"><svg width="50" height="40" viewBox="0 0 50 40"><circle cx="13" cy="12" r="5" fill="#fff"/><circle cx="25" cy="9" r="6" fill="#fff"/><circle cx="37" cy="12" r="5" fill="#fff"/><path d="M4 32c0-8 5-12 9-12s6 2 6 2c2-4 10-4 12 0 0 0 2-2 6-2s9 4 9 12z" fill="#fff"/></svg></div>
    <div class="svc-name">GROUP THERAPY</div>
    <div class="svc-text">To be the leading provider of outpatient psychiatric care.</div>
    <svg class="svc-go" width="18" height="18" viewBox="0 0 18 18"><circle cx="9" cy="9" r="9" fill="#fff"/><path d="M5 9h7M9 5l4 4-4 4" fill="none" stroke="#1a5fc0" stroke-width="2"/></svg>
  </div>
  <div class="svc-card green">
    <div class="svc-icon"><svg width="44" height="44" viewBox="0 0 44 44"><circle cx="15" cy="8" r="5" fill="#fff"/><circle cx="29" cy="8" r="5" fill="#fff"/><path d="M8 16h14v14h-4v10h-6V30H8zM22 16h14v14h-4v10h-6V30h-4z" fill="#fff"/><circle cx="22" cy="24" r="4" fill="#1a5fc0"/></svg></div>
    <div class="svc-name">FAMILY THERAPY</div>
    <div class="svc-text">To be the leading provider of outpatient psychiatric care.</div>
    <svg class="svc-go" width="18" height="18" viewBox="0 0 18 18"><circle cx="9" cy="9" r="9" fill="#fff"/><path d="M5 9h7M9 5l4 4-4 4" fill="none" stroke="#55ad0f" stroke-width="2"/></svg>
  </div>
  <div class="svc-card blue">
    <div class="svc-icon"><svg width="40" height="46" viewBox="0 0 40 46"><path d="M20 3l16 6v12c0 11-7 18-16 22C11 39 4 32 4 21V9z" fill="none" stroke="#fff" stroke-width="3"/><path d="M20 15v14M13 22h14" stroke="#fff" stroke-width="3"/></svg></div>
    <div class="svc-name">PARENTING CLASS</div>
    <div class="svc-text">To be the leading provider of outpatient psychiatric care.</div>
    <svg class="svc-go" width="18" height="18" viewBox="0 0 18 18"><circle cx="9" cy="9" r="9" fill="#fff"/><path d="M5 9h7M9 5l4 4-4 4" fill="none" stroke="#1a5fc0" stroke-width="2"/></svg>
  </div>
</div>

<section class="abs conditions">
  <div class="cond-text">
    <h2 class="cond-title">CONDITIONS WE TREAT</h2>
    <div class="cond-item"><svg width="14" height="12" viewBox="0 0 14 12"><path d="M0 6h11M7 1l5 5-5 5" fill="none" stroke="#fff" stroke-width="2"/></svg>Mood Disorders</div>
    <p class="cond-sub">Depression, Bipolar, Seasonal Affective Disorder, Cyclothymic Disorder, Premenstrual Dysphoric Disorder, Disruptive Mood Dysregulation Disorder</p>
    <div class="cond-item"><svg width="14" height="12" viewBox="0 0 14 12"><path d="M0 6h11M7 1l5 5-5 5" fill="none" stroke="#fff" stroke-width="2"/></svg>Anxiety Disorders</div>
    <div class="cond-item"><svg width="14" height="12" viewBox="0 0 14 12"><path d="M0 6h11M7 1l5 5-5 5" fill="none" stroke="#fff" stroke-width="2"/></svg>Common Disorders of Childhood</div>
    <div class="cond-item"><svg width="14" height="12" viewBox="0 0 14 12"><path d="M0 6h11M7 1l5 5-5 5" fill="none" stroke="#fff" stroke-width="2"/></svg>Psychotic Disorders</div>
  </div>
  <div class="cond-photo"><div role="img" aria-label="Photo of a counselor listening to a distressed young woman"></div></div>
</section>

<h2 class="abs sec-title" style="top:1748px">OUR FAQ'S</h2>
<div class="abs sec-rule" style="top:1792px"></div>

<div class="abs faq-list">
  <div class="faq-q open">What do I need to bring with me to my first visit?<svg width="12" height="10" viewBox="0 0 12 10"><path d="M1 1l5 4 5-4M1 5l5 4 5-4" fill="none" stroke="#fff" stroke-width="1.5"/></svg>
    <svg class="abs" style="right:-14px;top:3px" width="14" height="36" viewBox="0 0 14 36"><path d="M0 0l14 18L0 36z" fill="#55ad0f"/></svg></div>
  <div class="faq-q">How long do I have to wait to be seen?<svg width="10" height="12" viewBox="0 0 10 12"><path d="M1 1l4 5-4 5M5 1l4 5-4 5" fill="none" stroke="#55ad0f" stroke-width="1.5"/></svg></div>
  <div class="faq-q">What typs of insurance do you accept?<svg width="10" height="12" viewBox="0 0 10 12"><path d="M1 1l4 5-4 5M5 1l4 5-4 5" fill="none" stroke="#55ad0f" stroke-width="1.5"/></svg></div>
  <div class="faq-q">Why is my child not doing well in school?<svg width="10" height="12" viewBox="0 0 10 12"><path d="M1 1l4 5-4 5M5 1l4 5-4 5" fill="none" stroke="#55ad0f" stroke-width="1.5"/></svg></div>
</div>

<div class="abs faq-a">
  <h3>Answers to your questions:</h3>
  <div class="tick-line"><svg width="14" height="14" viewBox="0 0 14 14"><circle cx="7" cy="7" r="7" fill="#55ad0f"/><path d="M4 7h5M7 4l3 3-3 3" fill="none" stroke="#fff" stroke-width="1.5"/></svg>Nam libero tempore, cum soluta nobis est eligendi optio.</div>
  <div class="tick-line"><svg width="14" height="14" viewBox="0 0 14 14"><circle cx="7" cy="7" r="7" fill="#55ad0f"/><path d="M4 7h5M7 4l3 3-3 3" fill="none" stroke="#fff" stroke-width="1.5"/></svg>Eveniet ut et voluptates repudiandae sint et molestiae nonre.</div>
  <p>Insurance card, patient forms found on our Form's page.<br>Nemo enim ipsam voluptatem quia voluptas sit aspernatur aut odit aut fugit, sed quia consequuntur magni dolores eos qui ratione voluptatem sequi nesciunt. Neque porro quisquam est.</p>
</div>

<section class="abs news">
  <h2 class="abs sec-title" style="top:50px">LATEST NEWS</h2>
  <div class="abs sec-rule" style="top:94px"></div>
  <article class="news-item" style="left:100px">
    <div class="news-img" role="img" aria-label="Photo of a child with a teddy bear during a therapy session" style="background:linear-gradient(120deg,#e7dcd2,#c98a64 55%,#9fb4cc)"></div>
    <div class="news-body">
      <h4>Nemo enim ipsam</h4>
      <div class="meta"><span><svg width="10" height="10" viewBox="0 0 10 10"><rect x="0.5" y="1.5" width="9" height="8" fill="none" stroke="#55ad0f"/><path d="M0 4h10" stroke="#55ad0f"/></svg>12/9/16</span><span><svg width="10" height="10" viewBox="0 0 10 10"><circle cx="5" cy="3" r="2.5" fill="#55ad0f"/><path d="M0 10c0-4 10-4 10 0z" fill="#55ad0f"/></svg>Posted by admin</span></div>
      <p>To provide mental health services to children, adults, and the developmen tally disabled population that is cultur ally sensitive regardless of age.</p>
    </div>
  </article>
  <article class="news-item" style="left:635px">
    <div class="news-img" role="img" aria-label="Photo of a group therapy session in a bright room" style="background:linear-gradient(120deg,#6f6258,#c9b9a8 50%,#8c8f98)"></div>
    <div class="news-body">
      <h4>Sed ut perspiciatis</h4>
      <div class="meta"><span><svg width="10" height="10" viewBox="0 0 10 10"><rect x="0.5" y="1.5" width="9" height="8" fill="none" stroke="#55ad0f"/><path d="M0 4h10" stroke="#55ad0f"/></svg>12/9/16</span><span><svg width="10" height="10" viewBox="0 0 10 10"><circle cx="5" cy="3" r="2.5" fill="#55ad0f"/><path d="M0 10c0-4 10-4 10 0z" fill="#55ad0f"/></svg>Posted by admin</span></div>
      <p>To provide mental health services to children, adults, and the developmen tally disabled population that is cultur ally sensitive regardless of age.</p>
    </div>
  </article>
</section>

<footer class="abs site-footer">
  <svg class="foot-notch" width="1200" height="44" viewBox="0 0 1200 44" preserveAspectRatio="none"><path d="M0 0H1200L600 44z" fill="#efefef"/></svg>
  <h2 class="abs foot-title">CONTACT US</h2>
  <div class="abs foot-rule"></div>
  <div class="abs foot-contact">
    <span><svg width="34" height="34" viewBox="0 0 34 34"><circle cx="17" cy="17" r="15" fill="none" stroke="#fff" stroke-width="2"/><rect x="10" y="12" width="14" height="10" fill="none" stroke="#fff" stroke-width="1.6"/><path d="M10 12l7 6 7-6" fill="none" stroke="#fff" stroke-width="1.6"/></svg>hello@maplecrestbh.com</span>
    <span><svg width="34" height="34" viewBox="0 0 34 34"><circle cx="17" cy="17" r="15" fill="none" stroke="#fff" stroke-width="2"/><path d="M12 10l3 0 1.5 4-2 1.5a9 9 0 0 0 4 4l1.5-2 4 1.5v3a2 2 0 0 1-2 2A13 13 0 0 1 10 12a2 2 0 0 1 2-2z" fill="#fff"/></svg>180 047 3918</span>
  </div>
  <nav class="abs foot-links"><span>HOME</span><span>|</span><span>ABOUT US</span><span>|</span><span>SERVICES</span><span>|</span><span>CONDITIONS WE TREAT</span><span>|</span><span>NEW PATIENTS</span><span>|</span><span>CONTACT US</span></nav>
  <div class="abs foot-line"></div>
  <p class="abs copyright">Copyright © 2017 Maplecrest. All Right Reserved</p>
  <div class="abs social" aria-label="Social links"><span></span><span></span><span></span><span></span><span></span></div>
</footer>

</body>
</html>
```